Compression Arm Sleeve Packaging

We are a seller of sports compression arm sleeves. Our arm sleeves are used by athletes in just about every sport. Baseball, football, & basketball make up our largest customer base. We are in need of a product packaging design as a Vector image.

We would like design to feature the following:
Front of package:
Name of product: Arm Sleeve, our logo, brand name, website address, center of package will need to have no content so sleeve can be seen through package.

Back of package: Size chart, website address, logo, brand name, product care:
Machine Wash <80F
Do Not Dry Clean
Do Not Iron
Do Not Bleach
Hang Dry

I have included a few samples of other arm sleeve brands packaging. The grivka package i like the "Grivka" scrolling across package, the qmotive package i like the different colors, although I would not want the same colors, The vantrelp i like that the name of company, & the item are in bold. I do not like the basketball player on the front.

Misc Notes. I have included a pic of our logo, as well as our brand name. The font used for our brand name can be changed. The color of logo can also be changed if needed. Also i have attached a picture of our website name. The measurement chart does not need to look exactly as one i posted.
Thank you for looking!!!

Target Market(s)

Athletes - Youth & adult

Font styles to use
Sans Serif

Requirements
Must have
• Brand Name - Tarnhollow Sports
• Website: tarnhollowsports.example
• Logo
• Measurement chart (back of package)
• Product Care (back of package)
• I am very open to colors. I see i have to choose color combos. Regardless of the colors i choose I am not a designer. Use your judgement on what you think works.
Nice to have
• Would like a package where the color really pops. If our arm sleeve package is placed beside 10 other arm sleeve brands packaging I want to be sure our package would be the one that stands out without being corny. Packaging should appeal to extreme athletes. Font - Our font is PLQ glintmark, however it is not my favorite. If you have something you think looks better go with it. Again if i was a designer you would not be reading this. Create a package that you think will stand out to extreme athletes, and at the same time the future extreme athletes.
Should not have
• Boring packaging.

```html
<!DOCTYPE html>
<html lang="en">
<head>
<meta charset="utf-8">
<title>Tarnhollow Sports – Compression Arm Sleeve Package Front</title>
<link href="https://fonts.googleapis.com/css2?family=Orbitron:wght@700;900&display=swap" rel="stylesheet">
<style>
  :root {
    --backdrop-top: #8c8b8b;
    --backdrop-bottom: #ebebeb;
    --pack-yellow: #fbd13c;
    --pack-amber: #f2ac35;
    --pack-orange: #ea8a26;
    --ink: #0c0a08;
    --window: #ffffff;
  }
  * { margin: 0; padding: 0; box-sizing: border-box; }
  html, body { width: 1200px; height: 1200px; overflow: hidden; }
  body {
    background: linear-gradient(180deg, var(--backdrop-top), var(--backdrop-bottom));
    font-family: "Orbitron", sans-serif;
    font-weight: 900;
    color: var(--ink);
    position: relative;
  }
  .package-front {
    position: absolute;
    left: 267px; top: 128px;
    width: 666px; height: 943px;
    background: linear-gradient(180deg, var(--pack-yellow) 0%, var(--pack-amber) 55%, var(--pack-orange) 100%);
    overflow: hidden;
  }
  .display-window {
    position: absolute; inset: 0;
    width: 100%; height: 100%;
  }
  .brand-name {
    position: absolute;
    left: 0; top: 30px; width: 412px;
    text-align: center;
    font-size: 38px; line-height: 42px;
    font-weight: 900;
    letter-spacing: 0;
  }
  .brand-mark {
    position: absolute;
    left: 146px; top: 149px;
    width: 120px; height: 120px;
    border-radius: 50%;
    background: var(--ink);
  }
  .product-title {
    position: absolute;
    left: 0; top: 684px; width: 100%;
    text-align: center;
    font-weight: 900;
  }
  .product-kind { font-size: 37px; line-height: 44px; letter-spacing: 0.5px; }
  .product-name { font-size: 60px; line-height: 60px; letter-spacing: -1px; margin-top: -2px; }
  .product-tagline { font-size: 12.5px; line-height: 16px; letter-spacing: 0.8px; font-weight: 700; margin-top: 2px; }
  .feature-row {
    position: absolute;
    left: 0; top: 825px; width: 100%;
  }
  .feature {
    position: absolute;
    width: 160px; margin-left: -80px;
    text-align: center;
  }
  .feature-icon { display: block; margin: 0 auto; width: 64px; height: 64px; }
  .feature-label { font-size: 10.5px; line-height: 14px; font-weight: 700; margin-top: 11px; }
</style>
</head>
<body>
  <section class="package-front">
    <svg class="display-window" viewBox="0 0 666 943" preserveAspectRatio="none" role="img" aria-label="Clear window showing the arm sleeve inside">
      <polygon fill="var(--window)" points="482,0 666,0 666,245 0,700 0,535"/>
    </svg>

    <div class="brand-name">TARNHOLLOW<br>SPORTS</div>
    <div class="brand-mark"></div>

    <div class="product-title">
      <div class="product-kind">COMPRESSION</div>
      <div class="product-name">ARM SLEEVE</div>
      <div class="product-tagline">WITH OUR REINFORCED NON-SLIP SILICONE ELASTIC BAND</div>
    </div>

    <div class="feature-row">
      <div class="feature" style="left:79px">
        <svg class="feature-icon" viewBox="0 0 64 64" aria-hidden="true">
          <circle cx="32" cy="32" r="32" fill="var(--ink)"/>
          <path d="M20 14 L44 50 M20 14 L20 24 M20 14 L29 16" stroke="var(--pack-amber)" stroke-width="3" fill="none" stroke-linecap="round"/>
        </svg>
        <div class="feature-label">OVERALL<br>COMPRESSION</div>
      </div>
      <div class="feature" style="left:256px">
        <svg class="feature-icon" viewBox="0 0 64 64" aria-hidden="true">
          <circle cx="32" cy="32" r="32" fill="var(--ink)"/>
          <path d="M32 10 C24 24 17 32 17 40 A15 15 0 0 0 47 40 C47 32 40 24 32 10 Z" fill="var(--pack-amber)"/>
          <path d="M32 15 C26 26 22 33 22 40 A10 10 0 0 0 42 40 C42 33 38 26 32 15 Z" fill="var(--ink)"/>
          <path d="M24 43 L40 43 L32 51 Z" fill="var(--pack-amber)"/>
        </svg>
        <div class="feature-label">MOISTURE<br>WICKING MATERIAL</div>
      </div>
      <div class="feature" style="left:432px">
        <svg class="feature-icon" viewBox="0 0 64 64" aria-hidden="true">
          <circle cx="32" cy="32" r="32" fill="var(--ink)"/>
          <path d="M10 56 L56 8" stroke="var(--pack-amber)" stroke-width="1.5" stroke-dasharray="4 3"/>
        </svg>
        <div class="feature-label">FLAT SEAM<br>TECHNOLOGY</div>
      </div>
      <div class="feature" style="left:591px">
        <svg class="feature-icon" viewBox="0 0 64 64" aria-hidden="true">
          <circle cx="32" cy="32" r="32" fill="var(--ink)"/>
        </svg>
        <div class="feature-label">SIZE</div>
      </div>
    </div>
  </section>
</body>
</html>
```